RK Holdings Company brochure

require the design of a brochure for my company RK holdings which incorporates 2 separate companies specialising in home technology and security. Im not sure whether its going to be best to do one brochure with all the info in or 2 individual ones

Target Market(s)

Footballers and High net worth individuals

Industry/Entity Type

Information Technology

Font styles to use
Serif
Other font styles liked:
• Neuropol (this is the logo font)

Colors
ec1f27
000000
9d9d9d

Requirements
Must have
• 2 sections one for audio visual and 1 for security

```html
<!DOCTYPE html>
<html lang="en">
<head>
<meta charset="utf-8">
<title>RK Holdings Brochure Cover Spread</title>
<link rel="stylesheet" href="https://fonts.googleapis.com/css2?family=Open+Sans:wght@400;600&display=swap">
<style>
  :root {
    --red: #ec1f27;
    --red-deep: #9a1b20;
    --black: #0b0b0b;
    --grey: #9d9d9d;
    --white: #ffffff;
    --stage: #b9b9b9;
  }
  * { margin: 0; padding: 0; box-sizing: border-box; }
  html, body { width: 1200px; height: 789px; overflow: hidden; }
  body {
    background: var(--stage);
    font-family: "Open Sans", Arial, sans-serif;
    color: var(--white);
    position: relative;
  }
  .spread {
    position: absolute; left: 80px; top: 27px;
    width: 1040px; height: 735px;
    background: var(--black);
    overflow: hidden;
  }
  .photo { position: absolute; }
  .photo--lounge {
    left: 0; top: 0; width: 270px; height: 600px;
    background: linear-gradient(160deg, #2a1d18 0%, #5a3b2a 40%, #3a2a22 70%, #1a120e 100%);
  }
  .photo--cinema {
    left: 520px; top: 0; width: 520px; height: 560px;
    background: linear-gradient(175deg, #d8d2cc 0%, #8e7e80 25%, #4a2a3a 50%, #6b3f6e 75%, #3d2040 100%);
  }
  .about-panel {
    position: absolute; left: 270px; top: 0; width: 250px; height: 600px;
    background: linear-gradient(180deg, var(--red-deep) 0%, #7e1519 100%);
  }
  .curves { position: absolute; left: 0; top: 0; }
  .about { position: absolute; left: 288px; top: 95px; width: 215px; }
  .about__title { font-size: 13px; font-weight: 400; margin-bottom: 8px; }
  .about__text { font-size: 9.5px; line-height: 1.5; }
  .partner-badge { position: absolute; left: 320px; top: 405px; }
  .contact {
    position: absolute; font-size: 12px; line-height: 1.4;
    display: flex; gap: 6px; align-items: flex-start;
  }
  .contact svg { flex: none; margin-top: 2px; }
  .contact--address { left: 40px; top: 640px; }
  .contact--phone { left: 215px; top: 680px; }
  .contact--email { left: 395px; top: 650px; }
  .contact--web { left: 565px; top: 615px; }
  .brand {
    position: absolute; left: 830px; top: 500px;
    display: flex; align-items: center; gap: 10px;
    font-size: 18px; font-weight: 600; color: var(--white);
  }
  .brand__dot { width: 16px; height: 16px; border-radius: 50%; background: var(--red); }
</style>
</head>
<body>
  <main class="spread">
    <div class="photo photo--lounge" role="img" aria-label="Photo of a dark wood-panelled living room with a wall screen showing a home control menu"></div>
    <div class="about-panel"></div>
    <div class="photo photo--cinema" role="img" aria-label="Photo of a private home cinema with a large screen, domed ceiling and purple carpet"></div>

    <svg class="curves" width="1040" height="735" viewBox="0 0 1040 735" aria-hidden="true">
      <path d="M0,590 Q560,575 1040,300 L1040,735 L0,735 Z" fill="#d9d9d9"/>
      <path d="M0,600 Q560,585 1040,318 L1040,735 L0,735 Z" fill="var(--red)"/>
      <path d="M0,608 Q560,594 1040,334 L1040,735 L0,735 Z" fill="#ffffff"/>
      <path d="M0,616 Q560,604 1040,348 L1040,735 L0,735 Z" fill="var(--black)"/>
      <line x1="520" y1="0" x2="520" y2="735" stroke="#000" stroke-opacity="0.25"/>
    </svg>

    <section class="about">
      <h2 class="about__title">About us</h2>
      <p class="about__text">With offices in London and Newcastle, we design, install and service entertainment and control systems for our clients. The service is personal, unintimidating and of the highest quality. We create systems that enrich and support our clients' lives, giving them the technology they need without the compromise.</p>
    </section>

    <svg class="partner-badge" width="150" height="130" viewBox="0 0 150 130" role="img" aria-label="Partner dealer badge">
      <rect x="2" y="2" width="146" height="126" rx="12" fill="#f2f2f2"/>
      <rect x="12" y="58" width="126" height="60" rx="6" fill="var(--red)"/>
    </svg>

    <div class="contact contact--address">
      <svg width="10" height="13" viewBox="0 0 10 13"><path d="M5,0 A5,5 0 0 1 10,5 C10,8 5,13 5,13 C5,13 0,8 0,5 A5,5 0 0 1 5,0 Z" fill="var(--red)"/><circle cx="5" cy="5" r="2" fill="var(--black)"/></svg>
      <p>RK Holdings Ltd<br>Harwood Court<br>18-24 Elmstead Road<br>London<br>SW4 7QT</p>
    </div>
    <div class="contact contact--phone">
      <svg width="12" height="12" viewBox="0 0 12 12"><circle cx="6" cy="6" r="5" fill="none" stroke="var(--red)" stroke-width="1.3"/><path d="M4,3.5 L5,3.5 L5.5,5 L4.8,5.6 Q5.6,7 6.6,7.4 L7.2,6.6 L8.6,7.2 L8.5,8.3 Q5,8.5 3.6,4.6 Z" fill="var(--red)"/></svg>
      <p>0208 555 0192</p>
    </div>
    <div class="contact contact--email">
      <svg width="13" height="10" viewBox="0 0 13 10"><rect x="0.6" y="0.6" width="11.8" height="8.8" fill="none" stroke="var(--red)" stroke-width="1.2"/><path d="M0.6,0.6 L6.5,5.5 L12.4,0.6" fill="none" stroke="var(--red)" stroke-width="1.2"/></svg>
      <p>hello@rkholdings.co.uk</p>
    </div>
    <div class="contact contact--web">
      <svg width="12" height="12" viewBox="0 0 12 12"><circle cx="6" cy="6" r="5" fill="none" stroke="var(--red)" stroke-width="1.2"/><ellipse cx="6" cy="6" rx="2.2" ry="5" fill="none" stroke="var(--red)" stroke-width="1"/><line x1="1" y1="6" x2="11" y2="6" stroke="var(--red)" stroke-width="1"/></svg>
      <p>www.rkholdings.co.uk</p>
    </div>

    <div class="brand">
      <span class="brand__dot"></span>
      <span>RK Security</span>
    </div>
  </main>
</body>
</html>
```